Startup Web Design and Hosting Company Requiring Wow Brochure!

I am a web designer new to the business and need a format to market myself to local businesses. I have a website that defines clearly who I am and what I do. I need to carry this information onto an exciting, eye catching brochure. Please follow the general theme and layout of the website using vibrant colours. I would like to advertise the fact that I am a one stop shop - design, maintenance, hosting and full support. This brochure will communicate that a quality website starts at $499. Social media integration is an import feature to communicate on the brochure -facebook, twitter, linked in etc as well as SEO.
Website: www.maribethquoll.ca
Updates
Reason: Several of the designs are very great and I would like some time to see a few last revisions before I make a final decision. Some really great talent here.
Target Market(s)
Small business not yet on the web. Too busy to take on the task or not knowledgeable in this area.
Industry/Entity Type
Shop
Look and feel
Each slider illustrates characteristics of the customer's brand and the style your logo design should communicate.

```html
<!DOCTYPE html>
<html lang="en">
<head>
<meta charset="utf-8">
<title>Web Design &amp; Hosting Brochure</title>
<link href="https://fonts.googleapis.com/css2?family=Oswald:wght@500;600&family=Roboto+Condensed:wght@300;400&display=swap" rel="stylesheet">
<style>
:root{
  --red-top:#ec2029;
  --red-bottom:#c8141d;
  --blue-top:#1bb2ee;
  --blue-bottom:#0a7cc4;
  --navy:#1e5d8d;
  --heading-blue:#1c5c8c;
  --body-grey:#8c8c8c;
  --panel-top:#efefef;
  --panel-bottom:#ffffff;
  --white:#ffffff;
}
*{margin:0;padding:0;box-sizing:border-box}
html,body{width:1200px;height:865px;overflow:hidden;background:var(--white)}
.brochure{position:relative;width:1200px;height:865px;overflow:hidden;font-family:"Roboto Condensed",sans-serif}
.hero-photo{position:absolute;left:0;top:0;width:800px;height:560px;
  background:radial-gradient(ellipse at 55% 40%,#f4f1ee 0%,#e6e4e2 45%,#cfd3d8 100%)}
.services-panel{position:absolute;left:800px;top:0;width:400px;height:865px;
  background:linear-gradient(180deg,var(--panel-top),var(--panel-bottom))}
.shapes{position:absolute;left:0;top:0}
.tab-title{position:absolute;left:825px;top:10px;font-family:"Oswald",sans-serif;font-weight:500;
  font-size:46px;color:var(--white);letter-spacing:-0.5px;line-height:1.2}
.service{position:absolute;left:824px;width:358px}
.service h3{font-family:"Oswald",sans-serif;font-weight:600;font-size:19px;line-height:20px;
  color:var(--heading-blue);text-transform:uppercase;letter-spacing:-0.2px}
.service p{font-size:10.6px;line-height:11.6px;color:var(--body-grey);text-align:justify}
.feature{position:absolute;color:var(--white)}
.feature h2{font-family:"Oswald",sans-serif;font-weight:500;font-size:37px;line-height:36px;
  text-transform:uppercase;letter-spacing:-0.3px}
.feature p{font-size:14.2px;line-height:15px;text-align:justify}
.feature--blue p{font-size:12.6px;line-height:13.2px}
</style>
</head>
<body>
<main class="brochure">
  <div class="hero-photo" role="img" aria-label="Photo of a smiling web designer seated at a desk with a laptop in a bright office with a lamp, plant and bookshelf"></div>
  <div class="services-panel"></div>

  <svg class="shapes" width="1200" height="865" viewBox="0 0 1200 865" aria-hidden="true">
    <defs>
      <linearGradient id="redFill" x1="0" y1="0" x2="0" y2="1">
        <stop offset="0" stop-color="var(--red-top)"/><stop offset="1" stop-color="var(--red-bottom)"/>
      </linearGradient>
      <linearGradient id="blueFill" x1="0" y1="0" x2="0" y2="1">
        <stop offset="0" stop-color="var(--blue-top)"/><stop offset="1" stop-color="var(--blue-bottom)"/>
      </linearGradient>
    </defs>
    <path d="M0,526 L328,472 Q358,467 364,494 L402,865 L0,865 Z" fill="url(#redFill)"/>
    <path d="M348,540 Q344,506 380,500 L760,452 Q792,448 797,478 L800,865 L398,865 Z" fill="url(#blueFill)"/>
    <path d="M800,0 H1108 V58 Q1108,78 1088,80 L800,92 Z" fill="var(--navy)"/>
  </svg>

  <h1 class="tab-title">OUR SERVICES</h1>

  <section class="service" style="top:101px"><h3>Responsive Design</h3>
    <p>We create websites that are fully responsive and can adapt to any screen size. Try resizing your browser window or view this page on your mobile device to see it happen.</p></section>
  <section class="service" style="top:168px"><h3>Hosting Packages</h3>
    <p>Choose a package that’s right for your business and pay for only what you need. Feeling a little “techy”? We can help you manage your own sites content with minimal training.</p></section>
  <section class="service" style="top:236px"><h3>Maintenance</h3>
    <p>We have many maintenance options available that can accompany your web design package. Whether you need a little or a lot, we have a package that’s right for you.</p></section>
  <section class="service" style="top:302px"><h3>Support</h3>
    <p>Your website is finished, you’re on your way! Our relationship doesn’t end there. We’re here for you with a continued relationship of support to help you through any concerns or issues you may have. Real people, fast and effective resolutions. That’s our promise.</p></section>
  <section class="service" style="top:378px"><h3>Domain Registration</h3>
    <p>We can find a domain name that suits your business quickly and securely. Set up can be completed in 24 hrs or less. We can transfer your existing domain name to our hosting service with minimal interruption. We offer PanelDeck controls to make your webserver simple enough for you to manage should you chose to. We can also manage your entire setup, install and maintenance. The choice is completely up to you.</p></section>
  <section class="service" style="top:486px"><h3>Email Setup</h3>
    <p>Let us take the mystery out of email setup and configuration. Your package comes with unlimited email accounts on your domain. Email forwarders, spam protection, and ease of setup on any email app or device. We can walk you through the details or configuring your accounts and devices in minutes.</p></section>
  <section class="service" style="top:565px"><h3>Newsletter</h3>
    <p>Keeping in touch with customers is a key factor in business success. A newsletter themed to match your website is a great way to keep customers and find new ones. Visitors to your site can sign up to your periodic publication to receive updates on your products, services or get free tips from you. A great way to stay in touch with your customers and we do all the heavy lifting.</p></section>
  <section class="service" style="top:666px"><h3>Social Media Marketing</h3>
    <p style="margin-top:4px">The results are in and Social Media is the fastest growing medium to reach new customers. We can integrate your current platforms into your website to gain acknowledgement and to let visitors connect with you via your social media. Not into social media? not to worry, we can get you up and running in days. We can even do your posting, tweeting and any other publishing you may need.</p></section>
  <section class="service" style="top:763px"><h3>SEO</h3>
    <p>Search Engine Optimization, no need to panic. We can ensure your site and its collection of content are organized to meet search engine rules. Meta tags, headers, sitemap auto generation and submisssion, Seekwell Webmaster Tools and Analytics, Seekwell Authorship…we’ve got you covered. We make sure people can find you.</p></section>

  <section class="feature" style="left:26px;top:563px;width:301px"><h2>Web Design</h2>
    <p>Creating cutting edge, custom website designs to support your business needs. More than just a website, an integrated web solution using the latest technologies to attract and maintain customers for our clients. Working with you to develop a design that reflects your company’s vision.</p></section>
  <section class="feature" style="left:26px;top:734px;width:301px"><h2>Our Company Mission</h2>
    <p>Building websites and relationships on a foundation of quality, integrity, support and customer satisfaction.</p></section>

  <section class="feature feature--blue" style="left:414px;top:540px;width:358px"><h2>What We Promise</h2>
    <p style="font-size:14.2px;line-height:15px">No project is complete until the customer is completely satisfied.</p></section>
  <section class="feature feature--blue" style="left:414px;top:624px;width:358px"><h2>Hosting</h2>
    <p>Offering competitive hosting packages customized to suit your business needs. From multi-tenant to virtual private servers, we can help you choose the solution that best matches your requirements. We offer flexibility of control with your hosting package and even offer training to enable you to manage your site.</p></section>
  <section class="feature feature--blue" style="left:414px;top:751px;width:358px"><h2>Support</h2>
    <p>Our relationship does not end with the launch of your website. We are available to answer any questions or quickly resolve any issues to help you maintain and grow your online presence.</p></section>
</main>
</body>
</html>
```